Boutique custom software development company needs new business card

Our nearly 20 year old custom software development company would like to better include the fact that we are now providing Bitcoin services. These new services are B2B include education (how to acquire and securely hold Bitcoin) and integrating Bitcoin payments into existing ecommerce sites or other existing systems. Please keep the card clean and simple. Attached is our current design and some other files. vextorial.com

Target Market(s)

businesses owners interested in long term relationship

Industry/Entity Type

Custom software development and Bitcoin

Contact Information for Business Card

Dale Parker, dale@vextorial.com, vextorial.com, (888) 555-VXTRL

Font styles to use
Other font styles liked:
• monospace

Requirements
Must have
• double-sided
Nice to have
• clean and simple
Should not have
• physical address

```html
<!DOCTYPE html>
<html lang="en">
<head>
<meta charset="utf-8">
<title>Vextorial Business Card</title>
<link href="https://fonts.googleapis.com/css2?family=Montserrat:wght@400;500;700;800&family=Lato:wght@300;400&display=swap" rel="stylesheet">
<style>
  :root {
    --brand-blue: #3F73B8;
    --band-blue: #3A72B7;
    --brand-orange: #EE7B23;
    --brand-yellow: #FBBA16;
    --paper: #FFFFFF;
    --ink: #111111;
  }
  * { margin: 0; padding: 0; box-sizing: border-box; }
  html, body { width: 1200px; height: 1200px; overflow: hidden; background: var(--paper); }
  .canvas { position: relative; width: 1200px; height: 1200px; font-family: 'Montserrat', sans-serif; }
  .backdrop-top { position: absolute; left: 0; top: 0; width: 1200px; height: 586px; background: var(--brand-blue); }
  .stripe-orange { position: absolute; left: 0; top: 586px; width: 1200px; height: 14px; background: var(--brand-orange); }
  .stripe-yellow { position: absolute; left: 0; top: 600px; width: 1200px; height: 14px; background: var(--brand-yellow); }

  .card { position: absolute; left: 237px; width: 726px; height: 420px; }
  .card-front { top: 86px; background: var(--paper); }
  .card-back { top: 689px; background: var(--brand-blue); }

  .front-brand { position: absolute; left: 0; width: 100%; top: 112px; display: flex; justify-content: center; align-items: center; gap: 12px; }
  .front-brand .mark-square { width: 30px; height: 30px; background: var(--brand-orange); }
  .front-brand .brand-name { font-weight: 800; font-size: 42px; letter-spacing: 1px; color: var(--brand-blue); line-height: 1; }

  .identity { position: absolute; right: 399px; top: 242px; text-align: right; }
  .person-name { font-weight: 700; font-size: 41px; line-height: 1; letter-spacing: 0.5px; white-space: nowrap; }
  .person-name .first { color: var(--brand-orange); }
  .person-name .last { color: var(--brand-blue); }
  .person-email { margin-top: 6px; font-weight: 500; font-size: 19px; color: var(--ink); letter-spacing: 1px; }

  .divider { position: absolute; left: 355px; top: 247px; width: 2px; height: 55px; background: var(--brand-blue); }

  .contact-list { position: absolute; left: 373px; top: 245px; list-style: none; }
  .contact-list li { display: flex; align-items: center; height: 34px; font-weight: 500; font-size: 19px; color: var(--ink); letter-spacing: 1px; white-space: nowrap; }
  .contact-list svg { width: 24px; height: 24px; margin-right: 11px; }

  .services-band { position: absolute; left: 0; top: 362px; width: 100%; height: 33px; background: var(--band-blue); display: flex; justify-content: center; align-items: center; color: var(--paper); font-weight: 500; font-size: 19px; letter-spacing: 0.5px; white-space: nowrap; }

  .back-brand { position: absolute; left: 0; width: 100%; top: 160px; text-align: center; }
  .back-brand .brand-name { font-weight: 800; font-size: 68px; line-height: 1; color: var(--paper); letter-spacing: 1px; }
  .back-brand .tagline { margin-top: 8px; font-family: 'Lato', sans-serif; font-weight: 400; font-size: 25px; color: var(--paper); letter-spacing: -0.8px; }
</style>
</head>
<body>
<div class="canvas">
  <div class="backdrop-top"></div>
  <div class="stripe-orange"></div>
  <div class="stripe-yellow"></div>

  <section class="card card-front">
    <div class="front-brand">
      <span class="mark-square"></span>
      <span class="brand-name">VEXTORIAL</span>
    </div>

    <div class="identity">
      <p class="person-name"><span class="first">Dale</span> <span class="last">Parker</span></p>
      <p class="person-email">dale@vextorial.com</p>
    </div>

    <div class="divider"></div>

    <ul class="contact-list">
      <li>
        <svg viewBox="0 0 24 24" aria-hidden="true"><rect x="6" y="2" width="12" height="20" rx="2" fill="none" stroke="#3F73B8" stroke-width="2"/><line x1="10" y1="4.5" x2="14" y2="4.5" stroke="#3F73B8" stroke-width="1.2"/><circle cx="12" cy="18.5" r="1" fill="#3F73B8"/></svg>
        (888) 555-VXTRL
      </li>
      <li>
        <svg viewBox="0 0 24 24" aria-hidden="true" fill="none" stroke="#3F73B8" stroke-width="1.3"><circle cx="12" cy="12" r="10"/><ellipse cx="12" cy="12" rx="4.5" ry="10"/><line x1="2" y1="12" x2="22" y2="12"/><path d="M4 7h16M4 17h16"/><line x1="12" y1="2" x2="12" y2="22"/></svg>
        vextorial.com
      </li>
    </ul>

    <div class="services-band">Custom Software &bull; Bitcoin Education &amp; Payments</div>
  </section>

  <section class="card card-back">
    <div class="back-brand">
      <p class="brand-name">VEXTORIAL</p>
      <p class="tagline">developer of custom applications</p>
    </div>
  </section>
</div>
</body>
</html>
```